Business card design Needed for new logo / Construction business, home extensions and new builds

We need a business card design using our new logo files which i will attach to this project :)

We are a small construction business specialising in home extensions, new builds and property development. We are very ambitious and would appreciate professional and elegant designs for our new business card.

Very serious about using the services on MakerQuarry and recently acquired our new logo from here :)

Please get involved, i will feedback when i can as i am very busy but can respond daily, thanks

Target Market(s)

People that want to build onto their houses, new building developments or adding too their existing property

Industry/Entity Type

Construction

Contact Information for Business Card

Renwick Tolliver Construction, Lionel Ashby (Managing Director), Tel 07822254961, email - info@renwick-tolliver, www.renwick-tolliver.co.uk

Colors

Designer to choose colors to be used in the design.

Requirements
Must have
• I like a deep grey on the back please. A lot of you have provided black from and back, try mixing things up a little. The black looks cool 😎 Thanks

```html
<!DOCTYPE html>
<html lang="en">
<head>
<meta charset="utf-8">
<title>Renwick Tolliver Construction – Business Card</title>
<link rel="stylesheet" href="https://fonts.googleapis.com/css2?family=Open+Sans:wght@400;600;700&display=swap">
<style>
  :root {
    --stage: #333335;
    --card-front: #1e1e21;
    --card-back-light: #2c2c30;
    --card-back-dark: #151517;
    --silver: #d4d5d8;
    --silver-dark: #9a9ca0;
    --gold: #e2ad3b;
    --gold-light: #f3cf6a;
    --gold-dark: #b07d1c;
    --text: #f2f2f2;
  }
  * { box-sizing: border-box; margin: 0; padding: 0; }
  html, body { width: 1200px; height: 780px; overflow: hidden; }
  body {
    background: var(--stage);
    font-family: "Open Sans", sans-serif;
    display: flex;
    align-items: center;
    justify-content: center;
    gap: 30px;
  }
  .card {
    position: relative;
    width: 560px;
    height: 330px;
    border-radius: 4px;
    overflow: hidden;
    box-shadow: 0 12px 30px rgba(0,0,0,.45);
  }

  /* Back */
  .card-back { background: var(--card-back-dark); }
  .back-texture {
    position: absolute; inset: 0;
    background: linear-gradient(150deg, var(--card-back-light) 0%, #202023 45%, var(--card-back-dark) 100%);
  }
  .back-brand {
    position: absolute; right: 40px; top: 150px;
    display: flex; align-items: center; gap: 6px;
    font-size: 9px; font-weight: 600; letter-spacing: .04em;
    color: var(--silver);
  }
  .brand-dot {
    width: 12px; height: 12px; border-radius: 50%;
    background: var(--gold);
  }

  /* Front */
  .card-front { background: var(--card-front); color: var(--text); }
  .front-brand {
    position: absolute; left: 42px; top: 58px;
    display: flex; align-items: center; gap: 10px;
    font-size: 17px; font-weight: 600; letter-spacing: .03em;
    color: var(--silver);
  }
  .front-brand .brand-dot { width: 18px; height: 18px; }
  .address {
    position: absolute; left: 42px; top: 120px;
    font-size: 15px; line-height: 1.45;
  }
  .contact {
    position: absolute; left: 42px; top: 222px;
    list-style: none;
    font-size: 15px; line-height: 1;
  }
  .contact li { display: flex; align-items: center; gap: 12px; margin-bottom: 10px; }
  .contact svg { width: 16px; height: 16px; flex: none; }
  .person {
    position: absolute; right: 48px; top: 118px;
    text-align: right;
  }
  .person-name { font-size: 31px; font-weight: 700; line-height: 1.1; }
  .person-name .first { color: var(--silver); }
  .person-name .last { color: var(--gold); }
  .person-role { font-size: 15px; font-weight: 600; margin-top: 2px; }
  .accent-bar {
    position: absolute; right: 30px; top: 114px;
    width: 9px; height: 58px;
    background: linear-gradient(90deg, var(--gold-dark), var(--gold-light), var(--gold));
  }
</style>
</head>
<body>
  <section class="card card-back">
    <div class="back-texture" role="img" aria-label="Repeating glossy monogram pattern across a deep grey background"></div>
    <div class="back-brand"><span class="brand-dot"></span>Renwick Tolliver Construction</div>
  </section>

  <section class="card card-front">
    <div class="front-brand"><span class="brand-dot"></span>Renwick Tolliver Construction</div>

    <p class="address">Harlow Lane, Eastmere<br>Bramcott, BT4 7QD</p>

    <ul class="contact">
      <li>
        <svg viewBox="0 0 16 16" aria-hidden="true"><path fill="var(--gold)" d="M3.6 1.5l2.3 2.6-1.3 1.7c.9 2 2.6 3.7 4.6 4.6l1.7-1.3 2.6 2.3-1.3 2.2C7.1 13.9 2.1 8.9 1.4 3z"/></svg>
        07822254961
      </li>
      <li>
        <svg viewBox="0 0 16 16" aria-hidden="true"><circle cx="8" cy="8" r="6.5" fill="none" stroke="var(--gold)" stroke-width="1.5"/><path d="M1.5 8h13M8 1.5c-3 3.5-3 9.5 0 13M8 1.5c3 3.5 3 9.5 0 13" fill="none" stroke="var(--gold)" stroke-width="1.2"/></svg>
        info@renwick-tolliver.co.uk
      </li>
      <li>
        <svg viewBox="0 0 16 16" aria-hidden="true"><rect x="1" y="3.5" width="14" height="10" rx="1" fill="none" stroke="var(--gold)" stroke-width="1.5"/><path d="M1.5 4.5L8 9.5l6.5-5" fill="none" stroke="var(--gold)" stroke-width="1.5"/></svg>
        www.renwick-tolliver.co.uk
      </li>
    </ul>

    <div class="person">
      <h1 class="person-name"><span class="first">Lionel</span> <span class="last">Ashby</span></h1>
      <p class="person-role">Managing Director</p>
    </div>
    <div class="accent-bar"></div>
  </section>
</body>
</html>
```